Bespoke Builders Business Card Design

We need a business card for an established builder of high quality bespoke homes in Auckland and Northland. We build and renovate homes collaboratively facilitating effective communication between owners, builders, architects, suppliers and tradespeople. We have never built or renovated a home that leaks or has faults. We only use reliable materials. We have never been sued or had legal action taken against us. We are honest builders of bespoke homes not group mass produced homes. Our niche market is in character homes. We practice sustainability and have built a lot of coastal property. We have been in business for over thirty years . We would like to see natural colors of the environment sand,sea and maybe vegetation . The design should communicate quality, sustainability,fair pricing, open communication and the originality of bespoke building. And the fact that the builder is registered.

Industry/Entity Type

Business

Contact Information for Business Card

Rowan Tellick Builders
Ph. 021583917
18 Kestrel Rd Harwood Bay Auckland 0814
PO Box 927 Mangawhai 0583

```html
<!DOCTYPE html>
<html lang="en">
<head>
<meta charset="utf-8">
<title>Rowan Tellick Builders — Business Card</title>
<link rel="stylesheet" href="https://fonts.googleapis.com/css2?family=Bodoni+Moda:wght@600&family=Open+Sans:wght@400&display=swap">
<style>
  :root {
    --page: #e6e4df;
    --ink: #050505;
    --paper: #f7f7f8;
    --royal: #2e3192;
    --rule: #3a3a3a;
    --light-text: #f2f2f2;
    --card-w: 540px;
    --card-h: 310px;
  }
  * { margin: 0; padding: 0; box-sizing: border-box; }
  html, body {
    width: 1200px;
    height: 902px;
    overflow: hidden;
    background: var(--page);
  }
  .sheet {
    position: relative;
    width: 1200px;
    height: 902px;
    display: flex;
    align-items: center;
    justify-content: center;
    gap: 40px;
  }
  .card {
    position: relative;
    width: var(--card-w);
    height: var(--card-h);
    overflow: hidden;
    box-shadow: 0 6px 18px rgba(0,0,0,0.18);
  }

  /* Back face */
  .card-back {
    background: var(--ink);
    border: 5px solid var(--royal);
    display: flex;
    align-items: center;
    justify-content: center;
  }
  .card-back .brand-name {
    font-family: "Bodoni Moda", "Times New Roman", serif;
    font-weight: 600;
    font-size: 36px;
    letter-spacing: 1px;
    color: var(--light-text);
  }

  /* Front face */
  .card-front { background: var(--paper); }
  .card-front .wave {
    position: absolute;
    inset: 0;
    width: 100%;
    height: 100%;
  }
  .title-row {
    position: absolute;
    top: 46px;
    left: 0;
    right: 0;
    display: flex;
    align-items: center;
    gap: 10px;
  }
  .title-row .rule {
    flex: 1;
    height: 2px;
    background: var(--rule);
  }
  .title-row .brand-name {
    font-family: "Bodoni Moda", "Times New Roman", serif;
    font-weight: 600;
    font-size: 30px;
    color: var(--royal);
    white-space: nowrap;
  }
  .contact {
    position: absolute;
    left: 200px;
    right: 20px;
    top: 218px;
    text-align: center;
    font-family: "Open Sans", Arial, sans-serif;
    font-size: 15px;
    line-height: 23px;
    color: var(--light-text);
  }
</style>
</head>
<body>
<main class="sheet">
  <section class="card card-back" aria-label="Card back">
    <h1 class="brand-name">Rowan Tellick Builders</h1>
  </section>

  <section class="card card-front" aria-label="Card front">
    <svg class="wave" viewBox="0 0 540 310" preserveAspectRatio="none" aria-hidden="true">
      <path d="M0,222 C150,222 250,186 320,138 C380,98 430,76 540,74 L540,310 L0,310 Z" fill="var(--royal)"/>
      <path d="M0,242 C160,242 262,206 332,158 C392,116 442,96 540,94 L540,310 L0,310 Z" fill="var(--ink)"/>
    </svg>
    <div class="title-row">
      <span class="rule"></span>
      <h2 class="brand-name">Rowan Tellick Builders</h2>
      <span class="rule"></span>
    </div>
    <address class="contact" style="font-style:normal">
      <p class="phone">021583917</p>
      <p class="street">18 Kestrel Rd Harwood Bay Auckland 0814</p>
      <p class="postal">PO Box 927 Mangawhai 0583</p>
    </address>
  </section>
</main>
</body>
</html>
```